Revamp of existing namecard

Existingly, i've got a namecard that i would like to retain the main design. but there are some changes in my company and i would need to do some amendments to it.

We are a money transfer and money exchange company.
I need 2 different types of name card.
1. For individual name cards
the front to put the following:
Company name and logo
English Name, Chinese Name appointment
Mobile Number, Email and Website.
2 License number under the logo and name

the back of the name card to put
8 address: 7 Singapore and 1 Hong Kong branch addresses
8 Mobile Number of the corresponding addresses.

We would like to retain the name card front design
the name card back design can change but color to retain.

2nd name card is generic name card
Front:
Company name and logo
Branch Mobile Number, Branch Address, Email and Website.

Industry/Entity Type

remittance and money exchange

Contact Information for Business Card

I need 2 different types of name card. 1. For individual name cards the front to put the following: Company name and logo English Name, Chinese Name appointment Mobile Number, Email and Website. 2 License number under the logo and name the back of the name card to put 8 address: 7 Singapore and 1 Hong Kong branch addresses 8 Mobile Number of the corresponding addresses. We would like to retain the name card front design the name card back design can change but color to retain. 2nd name card is generic name card Front: the front to put the following: Company name and logo Branch Mobile Number, Branch Address, Email and Website. 2 License number under the logo and name

Requirements
Must have
• I need 2 different types of name card. 1. For individual name cards the front to put the following: Company name and logo English Name, Chinese Name appointment Mobile Number, Email and Website. 2 License number under the logo and name the back of the name card to put 8 address: 7 Singapore and 1 Hong Kong branch addresses 8 Mobile Number of the corresponding addresses. We would like to retain the name card front design the name card back design can change but color to retain. 2nd name card is generic name card Front: the front to put the following: Company name and logo Branch Mobile Number, Branch Address, Email and Website. 2 License number under the logo and name
Nice to have
• use back color code

```html
<!DOCTYPE html>
<html lang="en">
<head>
<meta charset="utf-8">
<title>Meridia name cards</title>
<link href="https://fonts.googleapis.com/css2?family=Montserrat:wght@400;500;600;700&family=Noto+Sans+TC:wght@700&display=swap" rel="stylesheet">
<style>
:root{
  --board:#2c3340;
  --panel-white:#ffffff;
  --panel-scene:#e6e6e3;
  --card-light:#fbfbfa;
  --card-dark:#2f3b4d;
  --card-dark-deep:#293444;
  --ink:#2a2f38;
  --accent:#5bb8d6;
  --map-light:#e3e5e8;
  --map-dark:#25303f;
  --muted-light:#c9d3de;
}
*{margin:0;padding:0;box-sizing:border-box}
html,body{width:1200px;height:3687px;overflow:hidden}
body{background:var(--board);font-family:'Montserrat',sans-serif;color:var(--ink);position:relative}
.panel{position:absolute;left:32px;width:1134px}
.panel--scene{background:var(--panel-scene)}
.panel--sheet{background:var(--panel-white)}
.panel--top{top:32px;height:989px}
.panel--sheet{top:1043px;height:1132px}
.panel--bottom{top:2203px;height:1415px}
.sheet-title{position:absolute;font-size:38px;font-weight:500;transform:translateX(-50%);white-space:nowrap}
.side-label{position:absolute;font-size:29px;font-weight:400;transform:translateX(-50%)}
.card{position:absolute;width:489px;height:280px;overflow:hidden}
.card--light{background:var(--card-light)}
.card--dark{background:var(--card-dark);color:#fff}
.map{position:absolute;border-radius:40% 45% 35% 40%}
.card--light .map{left:0;top:22px;width:320px;height:240px;background:radial-gradient(ellipse at 40% 45%,var(--map-light),rgba(227,229,232,0) 70%)}
.card--dark .map{left:20px;top:18px;width:450px;height:250px;background:radial-gradient(ellipse at 45% 50%,var(--map-dark),rgba(37,48,63,0) 72%)}
.brand{position:absolute;display:flex;align-items:center;gap:8px}
.brand-dot{width:22px;height:22px;border-radius:50%;background:var(--accent)}
.brand-name{font-size:29px;font-weight:700;letter-spacing:.5px;line-height:1;color:var(--ink)}
.card--dark .brand-name{color:#fff}
.license{position:absolute;font-size:11px;font-weight:700;letter-spacing:.6px}
.person{position:absolute;left:17px;top:118px}
.person-name{font-size:19px;font-weight:700;line-height:1.1}
.person-name-zh{font-family:'Noto Sans TC',sans-serif;font-size:17px;font-weight:700;line-height:1.2}
.person-role{font-size:11px;color:var(--accent);margin-top:3px}
.contacts{position:absolute;list-style:none}
.contacts li{display:flex;align-items:center;gap:6px;font-size:12px;font-weight:500;letter-spacing:.6px;height:19px}
.contacts svg,.address svg{width:11px;height:11px;fill:var(--accent);flex:none}
.address{position:absolute;left:18px;top:170px;display:flex;gap:10px;align-items:flex-start}
.address p{font-size:11px;font-weight:600;line-height:17px}
.address svg{width:14px;height:16px;margin-top:2px}
.branch-head{position:absolute;left:0;width:100%;text-align:center;font-size:16px;font-weight:600;display:flex;justify-content:center;align-items:center;gap:5px}
.branch-head svg{width:11px;height:13px;fill:var(--accent)}
.branch-head small{font-size:6px;color:var(--accent);font-weight:500;align-self:flex-end;margin-bottom:3px}
.branch{position:absolute;width:200px;text-align:center;font-size:7px;font-weight:600;line-height:11px}
.branch .tel{color:var(--accent);font-size:6.5px}
.pattern{position:absolute;inset:0;background:var(--card-dark-deep)}
.back-brand{position:absolute;left:0;top:112px;width:100%;display:flex;flex-direction:column;align-items:center}
.back-brand .brand{position:static}
.tagline{font-size:11px;font-weight:600;color:var(--accent);margin-top:4px;margin-left:30px}
</style>
</head>
<body>

<!-- Presentation: individual card -->
<section class="panel panel--scene panel--top">
  <div class="card card--dark" style="left:58px;top:354px">
    <div class="map" role="img" aria-label="Dotted world map in dark navy tones"></div>
    <div class="branch-head" style="top:16px"><svg viewBox="0 0 12 14"><path d="M6 0a5 5 0 0 0-5 5c0 4 5 9 5 9s5-5 5-9a5 5 0 0 0-5-5zm0 7a2 2 0 1 1 0-4 2 2 0 0 1 0 4z"/></svg>Singapore<small>Branch</small></div>
    <div class="branch" style="left:30px;top:46px">10 Market Street #01-00, 100001<br><span class="tel">+65 6000 0001</span></div>
    <div class="branch" style="left:259px;top:46px">22 River Valley #02-10, 100002<br><span class="tel">+65 6000 0002</span></div>
    <div class="branch" style="left:30px;top:89px">35 Bencoolen Road #03-20, 100003<br><span class="tel">+65 6000 0003</span></div>
    <div class="branch" style="left:259px;top:89px">48 Tanjong Street #04-30, 100004<br><span class="tel">+65 6000 0004</span></div>
    <div class="branch" style="left:30px;top:132px">51 Jurong Avenue #05-40, 100005<br><span class="tel">+65 6000 0005</span></div>
    <div class="branch" style="left:259px;top:132px">63 Tampines Road #06-50, 100006<br><span class="tel">+65 6000 0006</span></div>
    <div class="branch" style="left:144px;top:172px">77 Serangoon Road #07-60, 100007<br><span class="tel">+65 6000 0007</span></div>
    <div class="branch-head" style="top:208px"><svg viewBox="0 0 12 14"><path d="M6 0a5 5 0 0 0-5 5c0 4 5 9 5 9s5-5 5-9a5 5 0 0 0-5-5zm0 7a2 2 0 1 1 0-4 2 2 0 0 1 0 4z"/></svg>Hong Kong<small>Branch</small></div>
    <div class="branch" style="left:144px;top:236px">18 Kelvin Road Unit 1208, Causeway<br><span class="tel">+852 9000 0008</span></div>
  </div>
  <div class="card card--light" style="left:587px;top:354px">
    <div class="map" role="img" aria-label="Dotted world map in light grey tones"></div>
    <div class="brand" style="left:180px;top:26px"><span class="brand-dot"></span><span class="brand-name">MERIDIA</span></div>
    <div class="license" style="left:214px;top:58px">01234567 | 07654321</div>
    <div class="person"><div class="person-name">Marcus Lau</div><div class="person-name-zh">劉志明</div><div class="person-role">Director of Business Development</div></div>
    <ul class="contacts" style="left:266px;top:120px">
      <li><svg viewBox="0 0 12 12"><path d="M3 0h6a1 1 0 0 1 1 1v10a1 1 0 0 1-1 1H3a1 1 0 0 1-1-1V1a1 1 0 0 1 1-1zm0 2v7h6V2z"/></svg>+852 9000 1234</li>
      <li><svg viewBox="0 0 12 12"><path d="M2.5 0 5 3 3.5 4.5a7 7 0 0 0 4 4L9 7l3 2.5-1.5 2C5 11.5.5 7 .5 1.5z"/></svg>+852 9000 5678</li>
      <li><svg viewBox="0 0 12 12"><path d="M0 2h12v8H0zm1 1 5 4 5-4z"/></svg>marcus@meridia.com.hk</li>
      <li><svg viewBox="0 0 12 12"><circle cx="6" cy="6" r="6"/></svg>www.meridia.com.hk</li>
    </ul>
  </div>
</section>

<!-- Flat layout sheet -->
<section class="panel panel--sheet">
  <h2 class="sheet-title" style="left:564px;top:50px">card 1</h2>
  <span class="side-label" style="left:277px;top:122px">front</span>
  <span class="side-label" style="left:840px;top:122px">back</span>

  <div class="card card--light" style="left:53px;top:181px">
    <div class="map" role="img" aria-label="Dotted world map in light grey tones"></div>
    <div class="brand" style="left:180px;top:26px"><span class="brand-dot"></span><span class="brand-name">MERIDIA</span></div>
    <div class="license" style="left:214px;top:58px">01234567 | 07654321</div>
    <div class="person"><div class="person-name">Marcus Lau</div><div class="person-name-zh">劉志明</div><div class="person-role">Director of Business Development</div></div>
    <ul class="contacts" style="left:266px;top:120px">
      <li><svg viewBox="0 0 12 12"><path d="M3 0h6a1 1 0 0 1 1 1v10a1 1 0 0 1-1 1H3a1 1 0 0 1-1-1V1a1 1 0 0 1 1-1zm0 2v7h6V2z"/></svg>+852 9000 1234</li>
      <li><svg viewBox="0 0 12 12"><path d="M2.5 0 5 3 3.5 4.5a7 7 0 0 0 4 4L9 7l3 2.5-1.5 2C5 11.5.5 7 .5 1.5z"/></svg>+852 9000 5678</li>
      <li><svg viewBox="0 0 12 12"><path d="M0 2h12v8H0zm1 1 5 4 5-4z"/></svg>marcus@meridia.com.hk</li>
      <li><svg viewBox="0 0 12 12"><circle cx="6" cy="6" r="6"/></svg>www.meridia.com.hk</li>
    </ul>
  </div>

  <div class="card card--dark" style="left:600px;top:176px;height:289px">
    <div class="map" role="img" aria-label="Dotted world map in dark navy tones"></div>
    <div class="branch-head" style="top:16px"><svg viewBox="0 0 12 14"><path d="M6 0a5 5 0 0 0-5 5c0 4 5 9 5 9s5-5 5-9a5 5 0 0 0-5-5zm0 7a2 2 0 1 1 0-4 2 2 0 0 1 0 4z"/></svg>Singapore<small>Branch</small></div>
    <div class="branch" style="left:30px;top:46px">10 Market Street #01-00, 100001<br><span class="tel">+65 6000 0001</span></div>
    <div class="branch" style="left:259px;top:46px">22 River Valley #02-10, 100002<br><span class="tel">+65 6000 0002</span></div>
    <div class="branch" style="left:30px;top:89px">35 Bencoolen Road #03-20, 100003<br><span class="tel">+65 6000 0003</span></div>
    <div class="branch" style="left:259px;top:89px">48 Tanjong Street #04-30, 100004<br><span class="tel">+65 6000 0004</span></div>
    <div class="branch" style="left:30px;top:132px">51 Jurong Avenue #05-40, 100005<br><span class="tel">+65 6000 0005</span></div>
    <div class="branch" style="left:259px;top:132px">63 Tampines Road #06-50, 100006<br><span class="tel">+65 6000 0006</span></div>
    <div class="branch" style="left:144px;top:172px">77 Serangoon Road #07-60, 100007<br><span class="tel">+65 6000 0007</span></div>
    <div class="branch-head" style="top:212px"><svg viewBox="0 0 12 14"><path d="M6 0a5 5 0 0 0-5 5c0 4 5 9 5 9s5-5 5-9a5 5 0 0 0-5-5zm0 7a2 2 0 1 1 0-4 2 2 0 0 1 0 4z"/></svg>Hong Kong<small>Branch</small></div>
    <div class="branch" style="left:144px;top:240px">18 Kelvin Road Unit 1208, Causeway<br><span class="tel">+852 9000 0008</span></div>
  </div>

  <h2 class="sheet-title" style="left:564px;top:502px">card 2</h2>
  <span class="side-label" style="left:277px;top:545px">front</span>
  <span class="side-label" style="left:840px;top:545px">back</span>

  <div class="card card--light" style="left:53px;top:597px">
    <div class="map" role="img" aria-label="Dotted world map in light grey tones"></div>
    <div class="brand" style="left:100px;top:54px"><span class="brand-dot"></span><span class="brand-name">MERIDIA</span></div>
    <div class="license" style="left:132px;top:87px">01234567 | 07654321</div>
    <div class="address"><svg viewBox="0 0 12 14"><path d="M6 0a5 5 0 0 0-5 5c0 4 5 9 5 9s5-5 5-9a5 5 0 0 0-5-5zm0 7a2 2 0 1 1 0-4 2 2 0 0 1 0 4z"/></svg><p>Unit 1208, 12th Floor<br>Harbour Point Tower<br>18 Kelvin Road, Causeway Bay</p></div>
    <ul class="contacts" style="left:283px;top:162px">
      <li><svg viewBox="0 0 12 12"><path d="M3 0h6a1 1 0 0 1 1 1v10a1 1 0 0 1-1 1H3a1 1 0 0 1-1-1V1a1 1 0 0 1 1-1zm0 2v7h6V2z"/></svg>+852 9000 1234</li>
      <li><svg viewBox="0 0 12 12"><path d="M2.5 0 5 3 3.5 4.5a7 7 0 0 0 4 4L9 7l3 2.5-1.5 2C5 11.5.5 7 .5 1.5z"/></svg>+852 9000 5678</li>
      <li><svg viewBox="0 0 12 12"><path d="M0 2h12v8H0zm1 1 5 4 5-4z"/></svg>marcus@meridia.com.hk</li>
      <li><svg viewBox="0 0 12 12"><circle cx="6" cy="6" r="6"/></svg>www.meridia.com.hk</li>
    </ul>
  </div>

  <div class="card card--dark" style="left:600px;top:593px;height:288px">
    <div class="pattern" role="img" aria-label="Repeating brand pattern in dark navy"></div>
    <div class="back-brand"><div class="brand"><span class="brand-dot"></span><span class="brand-name">MERIDIA</span></div><span class="tagline">remittance and money exchange</span></div>
  </div>
</section>

<!-- Presentation: generic card -->
<section class="panel panel--scene panel--bottom">
  <div class="card card--dark" style="left:58px;top:567px">
    <div class="pattern" role="img" aria-label="Repeating brand pattern in dark navy"></div>
    <div class="back-brand"><div class="brand"><span class="brand-dot"></span><span class="brand-name">MERIDIA</span></div><span class="tagline">remittance and money exchange</span></div>
  </div>
  <div class="card card--light" style="left:587px;top:567px">
    <div class="map" role="img" aria-label="Dotted world map in light grey tones"></div>
    <div class="brand" style="left:100px;top:54px"><span class="brand-dot"></span><span class="brand-name">MERIDIA</span></div>
    <div class="license" style="left:132px;top:87px">01234567 | 07654321</div>
    <div class="address"><svg viewBox="0 0 12 14"><path d="M6 0a5 5 0 0 0-5 5c0 4 5 9 5 9s5-5 5-9a5 5 0 0 0-5-5zm0 7a2 2 0 1 1 0-4 2 2 0 0 1 0 4z"/></svg><p>Unit 1208, 12th Floor<br>Harbour Point Tower<br>18 Kelvin Road, Causeway Bay</p></div>
    <ul class="contacts" style="left:283px;top:162px">
      <li><svg viewBox="0 0 12 12"><path d="M3 0h6a1 1 0 0 1 1 1v10a1 1 0 0 1-1 1H3a1 1 0 0 1-1-1V1a1 1 0 0 1 1-1zm0 2v7h6V2z"/></svg>+852 9000 1234</li>
      <li><svg viewBox="0 0 12 12"><path d="M2.5 0 5 3 3.5 4.5a7 7 0 0 0 4 4L9 7l3 2.5-1.5 2C5 11.5.5 7 .5 1.5z"/></svg>+852 9000 5678</li>
      <li><svg viewBox="0 0 12 12"><path d="M0 2h12v8H0zm1 1 5 4 5-4z"/></svg>marcus@meridia.com.hk</li>
      <li><svg viewBox="0 0 12 12"><circle cx="6" cy="6" r="6"/></svg>www.meridia.com.hk</li>
    </ul>
  </div>
</section>

</body>
</html>
```